Building Design company needing a letterhead

We need a letter head for our Building Design company to send letters etc. to our clients, consultants, councils etc. We would like to see our logo used and company colours. I have attached our style guide and an example of our current letterheads. Top left we would like our logo, top right we would like the company details and at the footer we would like some sort of image/design etc. that suits our brand. I like the Tarrow Design letterhead attached.

Target Market(s)

Professionals, Councils, Consultants, Mums & Dads

Industry/Entity Type

Architecture

Other font styles liked:
• refer the design style guide

Colors
f37122
000000
1b1b1b

Requirements
Must have
• Must have the minimum of a logo, company details and footer
Nice to have
• An image/design made for the footer that would suite our brand and website at www.corvanplans.com.au. Also it would be nice to include the KMEOT logo somewhere perhaps included in the footer.
Should not have
• Large images in the header. I just want the logo and company details.

```html
<!DOCTYPE html>
<html lang="en">
<head>
<meta charset="utf-8">
<title>Corvan Plans Letterhead</title>
<link rel="stylesheet" href="https://fonts.googleapis.com/css2?family=Michroma&display=swap">
<style>
  :root {
    --brand-orange: #e55a27;
    --ink-dark: #1b1b1b;
    --backdrop: #878787;
    --paper: #ffffff;
    --watermark: #f1f1f1;
    --on-orange: #ffffff;
  }
  * { box-sizing: border-box; margin: 0; padding: 0; }
  html, body {
    width: 847px; height: 1200px; overflow: hidden;
    background: var(--backdrop);
  }
  .letterhead {
    position: absolute; left: 70px; top: 70px;
    width: 708px; height: 1059px;
    background: var(--paper);
    font-family: "Michroma", sans-serif;
    font-variant: small-caps;
    color: var(--on-orange);
  }
  .header-band {
    position: absolute; left: 0; top: 0;
    width: 100%; height: 108px;
    background: var(--brand-orange);
  }
  .brand-block {
    position: absolute; left: 52px; top: 35px;
    width: 180px; height: 74px;
    background: var(--paper);
    display: flex; align-items: center; justify-content: center; gap: 8px;
  }
  .brand-mark {
    width: 12px; height: 12px; background: var(--brand-orange);
  }
  .brand-name {
    font-variant: normal; text-transform: uppercase;
    font-size: 12.5px; letter-spacing: 0.5px;
    color: var(--ink-dark);
  }
  .contact-block {
    position: absolute; right: 34px; top: 25px;
    text-align: right; font-size: 9.5px; letter-spacing: 1px;
    line-height: 1;
  }
  .contact-name { margin-bottom: 5px; font-size: 10.5px; }
  .contact-role { margin-bottom: 11px; }
  .contact-line {
    display: flex; justify-content: flex-end; align-items: center;
    gap: 7px; margin-bottom: 8px; margin-right: -9px;
  }
  .contact-line svg { width: 9px; height: 9px; flex: none; }
  .watermark {
    position: absolute; left: 0; top: 470px; width: 100%;
    text-align: center; font-variant: normal; text-transform: uppercase;
    font-size: 54px; letter-spacing: 2px;
    color: var(--watermark);
  }
  .footer-band {
    position: absolute; left: 0; bottom: 0;
    width: 100%; height: 67px;
    background: var(--brand-orange);
    text-align: center; font-size: 9.5px; letter-spacing: 1.2px;
    padding-top: 20px; line-height: 18px;
  }
</style>
</head>
<body>
  <main class="letterhead">
    <header class="header-band">
      <div class="brand-block">
        <span class="brand-mark"></span>
        <span class="brand-name">Corvan Plans</span>
      </div>
      <div class="contact-block">
        <p class="contact-name">John Smith</p>
        <p class="contact-role">Deisgnation</p>
        <p class="contact-line">(123) 456-7890
          <svg viewBox="0 0 10 10"><path d="M3 1 L4.5 1.4 L4 3.3 L3.3 3.6 Q3.6 5.8 5.6 6.9 L6.1 6.3 L8 6.6 L8.2 8.4 Q7 9.3 5.5 8.6 Q1.6 6.6 1.7 2.2 Z" fill="var(--on-orange)"/></svg>
        </p>
        <p class="contact-line">info@companyname.com
          <svg viewBox="0 0 10 10"><rect x="1" y="2.5" width="8" height="5.5" fill="var(--on-orange)"/><path d="M1 2.5 L5 5.6 L9 2.5" fill="none" stroke="var(--brand-orange)" stroke-width="0.8"/></svg>
        </p>
        <p class="contact-line">companyname.com
          <svg viewBox="0 0 10 10" fill="none" stroke="var(--on-orange)" stroke-width="0.8"><circle cx="5" cy="5" r="4"/><ellipse cx="5" cy="5" rx="1.8" ry="4"/><path d="M1 5 H9 M1.6 3 H8.4 M1.6 7 H8.4"/></svg>
        </p>
      </div>
    </header>

    <p class="watermark" aria-hidden="true">Corvan Plans</p>

    <footer class="footer-band">
      <p>Address line1, address line2</p>
      <p>country - 123456</p>
    </footer>
  </main>
</body>
</html>
```